Exciting new vermouth brand needs a brilliant label!

We need a label design for an exciting new premium Italian Vermouth brand called Brunallo Vermouth.

Brunallo Vermouth is based on a recipe that has been handed down for four generations and is made in the traditional way in the Piedmonte region of Northern Italy.

Brunallo, which means 'heavenly' in Italian has been designed to elevate classic cocktails such as the Negroni, Americano and Manhattan with a base of Italian wine blended with botanicals such as wormwood, orange peel, rhubarb and cinchona. It has a delicately balanced bittersweet profile with hints of vanilla and citrus.

Its competitors include brands such as Doralte Mirena, Bellusi and Grevano (see the uploaded brief for more examples).

The label is for a 50cl dark bottle (please refer to the uploaded brief) and should be based on maximum dimensions of 70mm (width) x 110mm (height). There is no limit to embellishments such as foil printing, embossing or any other premium finishes. The label does not necessarily need to be rectangular.

Feedback will be given quickly and constructively after submissions to ensure that the process is as fair and useful as possible for everyone.

Target Market(s)

25-45 year old Europeans, 50:50 female:male

Industry/Entity Type

Wine / Spirits / Vermouth

Requirements
Must have
• Fantastic design that is distinct from competitors, a premium feel and great lettering.
Should not have
• Generic images or patterns that do not relate to the brand (Brunallo) or the product

```html
<!DOCTYPE html>
<html lang="en">
<head>
<meta charset="utf-8">
<title>Brunallo Vermouth – Label Range</title>
<link rel="stylesheet" href="https://fonts.googleapis.com/css2?family=Michroma&family=Lexend:wght@400;600;700&display=swap">
<style>
  :root {
    --page-light: #ffffff;
    --page-dark: #000000;
    --ink-dark: #3a3b3d;
    --paper: #ffffff;
    --mono-grey: #a3a3a5;
    --teal: #00cc99;
    --blue: #5599f5;
    --amber: #ffb60d;
    --violet: #9a6fe0;
  }
  html, body { margin: 0; padding: 0; overflow: hidden; }
  .canvas { position: relative; width: 1200px; height: 2630px; background: var(--page-light); overflow: hidden; }
  .range-band { position: absolute; left: 0; top: 1432px; width: 1200px; height: 1198px; background: var(--page-dark); }
  .label { position: absolute; overflow: visible; }
  .label--mono   { --accent: var(--mono-grey); --ink: var(--mono-grey); --paper-fill: transparent; --edge: transparent; }
  .label--teal   { --accent: var(--teal);   --ink: var(--ink-dark); --paper-fill: var(--paper); --edge: #2a2a2a; }
  .label--blue   { --accent: var(--blue);   --ink: var(--ink-dark); --paper-fill: var(--paper); --edge: #2a2a2a; }
  .label--amber  { --accent: var(--amber);  --ink: var(--ink-dark); --paper-fill: var(--paper); --edge: transparent; }
  .label--violet { --accent: var(--violet); --ink: var(--ink-dark); --paper-fill: var(--paper); --edge: transparent; }
  .label__paper { fill: var(--paper-fill); stroke: var(--edge); stroke-width: 1.2; }
  .label__band--accent { fill: none; stroke: var(--accent); stroke-width: 26; }
  .label__band--ink { fill: none; stroke: var(--ink); stroke-width: 26; }
  .label__hair--ink { fill: none; stroke: var(--ink); stroke-width: 3; }
  .label__hair--accent { fill: none; stroke: var(--accent); stroke-width: 3; }
  .label__kicker { font-family: "Lexend", sans-serif; font-weight: 700; font-size: 22px; letter-spacing: 2px; fill: var(--ink); }
  .label__name { font-family: "Michroma", sans-serif; font-size: 46px; fill: var(--ink); }
  .label__style { font-family: "Lexend", sans-serif; font-weight: 400; font-size: 25px; letter-spacing: 1px; fill: var(--ink); }
  .label__strip { fill: var(--ink); }
  .label__serve { font-family: "Lexend", sans-serif; font-weight: 600; font-size: 14px; fill: var(--paper); }
  .label--mono .label__serve { fill: #ffffff; }
  .label__volume { font-family: "Lexend", sans-serif; font-weight: 700; font-size: 13px; fill: var(--ink); }
  .defs-holder { position: absolute; width: 0; height: 0; }
</style>
</head>
<body>
<main class="canvas">
  <svg class="defs-holder" aria-hidden="true">
    <defs>
      <path id="kicker-curve" d="M112 168 A96 96 0 0 1 288 168"/>
      <symbol id="label-art" viewBox="0 0 400 400">
        <circle class="label__paper" cx="200" cy="200" r="199"/>
        <path class="label__band--accent" d="M26.9 143.8 A182 182 0 0 1 373.1 143.8"/>
        <path class="label__band--ink" d="M373.1 256.2 A182 182 0 0 1 26.9 256.2"/>
        <path class="label__hair--ink" d="M64.1 136.6 A150 150 0 0 1 335.9 136.6"/>
        <path class="label__hair--accent" d="M335.9 263.4 A150 150 0 0 1 64.1 263.4"/>
        <text class="label__kicker" text-anchor="middle"><textPath href="#kicker-curve" startOffset="50%">VERMOUTH</textPath></text>
        <text class="label__name" x="200" y="219" text-anchor="middle" textLength="376" lengthAdjust="spacingAndGlyphs">BRUNALLO</text>
        <text class="label__style" x="200" y="256" text-anchor="middle">SWEET ROSSO</text>
        <path class="label__strip" d="M96 272 H304 L296 292 H104 Z"/>
        <text class="label__serve" x="200" y="287" text-anchor="middle">SERVED CHILLED</text>
        <text class="label__volume" x="200" y="312" text-anchor="middle">750ml</text>
      </symbol>
    </defs>
  </svg>

  <svg class="label label--mono" style="left:440px;top:85px;width:300px;height:300px" viewBox="0 0 400 400" role="img" aria-label="Brunallo Vermouth label, single-colour version"><use href="#label-art"/></svg>
  <svg class="label label--teal" style="left:113px;top:630px;width:400px;height:400px" viewBox="0 0 400 400" role="img" aria-label="Brunallo Vermouth label, teal"><use href="#label-art"/></svg>
  <svg class="label label--blue" style="left:671px;top:630px;width:400px;height:400px" viewBox="0 0 400 400" role="img" aria-label="Brunallo Vermouth label, blue"><use href="#label-art"/></svg>

  <section class="range-band" aria-label="Colour range">
    <svg class="label label--teal" style="left:400px;top:100px;width:400px;height:400px" viewBox="0 0 400 400" role="img" aria-label="Teal label"><use href="#label-art"/></svg>
    <svg class="label label--amber" style="left:52px;top:398px;width:400px;height:400px" viewBox="0 0 400 400" role="img" aria-label="Amber label"><use href="#label-art"/></svg>
    <svg class="label label--violet" style="left:746px;top:398px;width:400px;height:400px" viewBox="0 0 400 400" role="img" aria-label="Violet label"><use href="#label-art"/></svg>
    <svg class="label label--blue" style="left:405px;top:698px;width:400px;height:400px" viewBox="0 0 400 400" role="img" aria-label="Blue label"><use href="#label-art"/></svg>
  </section>
</main>
</body>
</html>
```